Business cards and stationary design

We just completed the design of our new logo and we need to print new business cards and letterhead for our nonprofit. We are looking for a fresh new design that shows off our new logo. On letterhead, we must have a column on the right or left to include our Board of Directors (up to 45 names) (see attachment)

Industry/Entity Type

Non-Profit

Contact Information for Business Card

Standard business card with name, title, Company name, mailing address phone numbers, email address and website. Tagline on back "Bringing the homeless home"

Font styles to use
Sans Serif

Requirements
Must have
• include pertinent information above
• new logo
• fonts compatible with logo
• should use logo colors only
Nice to have
• tag lines

```html
<!DOCTYPE html>
<html lang="en">
<head>
<meta charset="utf-8">
<title>Shelter Bridge Center – Business Card</title>
<link rel="stylesheet" href="https://fonts.googleapis.com/css2?family=Roboto:wght@400;500&family=Roboto+Condensed:wght@700&display=swap">
<style>
  :root {
    --page: #343436;
    --card: #1e1e20;
    --teal: #1b9dc0;
    --red: #e0262b;
    --white: #f2f2f2;
    --divider: #8a8a8a;
  }
  html, body {
    margin: 0;
    width: 1200px;
    height: 900px;
    overflow: hidden;
    background: var(--page);
    font-family: "Roboto", sans-serif;
  }
  .card {
    position: absolute;
    left: 290px;
    width: 620px;
    height: 354px;
    background: var(--card);
    box-shadow: 0 6px 18px rgba(0,0,0,0.45);
    color: var(--white);
  }
  .card-front { top: 70px; }
  .card-back { top: 476px; }

  .brand {
    position: absolute;
    top: 128px;
    left: 0;
    right: 0;
    display: flex;
    align-items: center;
    justify-content: center;
    gap: 14px;
  }
  .brand-dot {
    width: 16px;
    height: 16px;
    border-radius: 50%;
    background: var(--teal);
  }
  .brand-name {
    font-family: "Roboto", sans-serif;
    font-weight: 500;
    font-size: 30px;
    letter-spacing: 3px;
    text-transform: uppercase;
    color: var(--teal);
  }
  .front-web {
    position: absolute;
    top: 232px;
    left: 0;
    right: 0;
    text-align: center;
    font-size: 15px;
    letter-spacing: 7px;
    color: var(--white);
  }

  .identity {
    position: absolute;
    top: 96px;
    left: 150px;
    width: 170px;
    text-align: right;
  }
  .person-name {
    font-family: "Roboto Condensed", sans-serif;
    font-weight: 700;
    font-size: 32px;
    line-height: 1;
    color: var(--teal);
    text-transform: uppercase;
  }
  .person-title {
    font-family: "Roboto Condensed", sans-serif;
    font-weight: 700;
    font-size: 16px;
    color: var(--red);
    text-transform: uppercase;
    margin-top: 2px;
  }
  .divider {
    position: absolute;
    top: 82px;
    left: 340px;
    width: 1px;
    height: 90px;
    background: var(--divider);
  }
  .contact {
    position: absolute;
    top: 86px;
    left: 362px;
  }
  .contact-company {
    font-weight: 500;
    font-size: 17px;
    margin-bottom: 6px;
  }
  .contact-row {
    display: flex;
    align-items: center;
    gap: 8px;
    font-size: 15px;
    line-height: 21px;
  }
  .contact-row svg { width: 12px; height: 12px; fill: var(--teal); flex: none; }
  .address {
    position: absolute;
    left: 46px;
    bottom: 62px;
    display: flex;
    align-items: center;
    gap: 8px;
    font-size: 16px;
  }
  .address svg { width: 14px; height: 18px; fill: var(--teal); }
</style>
</head>
<body>
  <section class="card card-front">
    <div class="brand">
      <span class="brand-dot"></span>
      <span class="brand-name">Shelter Bridge Center</span>
    </div>
    <div class="front-web">www.shelterbridge.org</div>
  </section>

  <section class="card card-back">
    <div class="identity">
      <div class="person-name">Mara Ellison</div>
      <div class="person-title">CEO/Founder</div>
    </div>
    <div class="divider"></div>
    <div class="contact">
      <div class="contact-company">Shelter Bridge Center</div>
      <div class="contact-row">
        <svg viewBox="0 0 24 24"><path d="M6.6 10.8a15.1 15.1 0 0 0 6.6 6.6l2.2-2.2a1 1 0 0 1 1-.25 11.4 11.4 0 0 0 3.6.57 1 1 0 0 1 1 1V20a1 1 0 0 1-1 1A17 17 0 0 1 3 4a1 1 0 0 1 1-1h3.5a1 1 0 0 1 1 1c0 1.25.2 2.45.57 3.57a1 1 0 0 1-.25 1z"/></svg>
        <span>555 201 7734</span>
      </div>
      <div class="contact-row">
        <svg viewBox="0 0 24 24"><path d="M2 5h20v14H2z M2 5l10 8 10-8" /></svg>
        <span>mara@shelterbridge.org</span>
      </div>
      <div class="contact-row">
        <svg viewBox="0 0 24 24"><circle cx="12" cy="12" r="10"/></svg>
        <span>www.shelterbridge.org</span>
      </div>
    </div>
    <div class="address">
      <svg viewBox="0 0 24 30"><path d="M12 0a10 10 0 0 0-10 10c0 7.5 10 20 10 20s10-12.5 10-20A10 10 0 0 0 12 0zm0 14a4 4 0 1 1 0-8 4 4 0 0 1 0 8z"/></svg>
      <span>1420 Birchwood Road, Fairview, Alaska 99501</span>
    </div>
  </section>
</body>
</html>
```